Business card for medical clinic

I need an upmarket, modern medical/health business card for my clinic

Contact Information for Business Card

name, address, email, qr code

```html
<!DOCTYPE html>
<html lang="en">
<head>
<meta charset="UTF-8">
<title>Meridian Care Clinic – Business Card</title>
<link href="https://fonts.googleapis.com/css2?family=Cinzel:wght@500&family=Arimo:wght@400&display=swap" rel="stylesheet">
<style>
  :root {
    --bg: #d2d2d2;
    --card: #ffffff;
    --navy: #1b2a4e;
    --brand-blue: #1a6aa3;
    --sky: #29abe2;
    --ink: #333840;
    --rule: #8fc3e3;
  }
  * { margin: 0; padding: 0; box-sizing: border-box; }
  html, body { width: 1200px; height: 915px; overflow: hidden; }
  body {
    background: var(--bg);
    display: flex;
    flex-direction: column;
    align-items: center;
    justify-content: center;
    gap: 35px;
  }
  .card {
    position: relative;
    width: 700px;
    height: 400px;
    background: var(--card);
    border-radius: 22px;
    overflow: hidden;
    box-shadow: 0 8px 18px rgba(0,0,0,0.18);
  }
  .card__edge {
    position: absolute;
    left: 0; right: 0; bottom: 0;
    height: 10px;
    background: linear-gradient(90deg, var(--navy), var(--sky));
  }
  .brand {
    display: flex;
    align-items: center;
    gap: 16px;
    font-family: "Cinzel", serif;
    font-weight: 500;
    color: var(--brand-blue);
    letter-spacing: 0.06em;
    line-height: 1.05;
  }
  .brand__dot {
    border-radius: 50%;
    background: var(--brand-blue);
    flex-shrink: 0;
  }
  .card--front .brand {
    position: absolute;
    left: 50%; top: 50%;
    transform: translate(-50%, -50%);
    font-size: 42px;
  }
  .card--front .brand__dot { width: 26px; height: 26px; }
  .card--back .brand {
    position: absolute;
    left: 50px; top: 190px;
    font-size: 26px;
    gap: 12px;
  }
  .card--back .brand__dot { width: 18px; height: 18px; }
  .divider {
    position: absolute;
    left: 370px; top: 70px;
    width: 1px; height: 200px;
    background: var(--rule);
  }
  .contact {
    position: absolute;
    left: 395px; top: 68px;
    font-family: "Arimo", sans-serif;
    color: var(--ink);
    font-size: 15px;
    line-height: 1.3;
  }
  .contact__name {
    font-family: "Cinzel", serif;
    font-weight: 500;
    color: var(--brand-blue);
    font-size: 24px;
    letter-spacing: 0.04em;
    line-height: 1.1;
  }
  .contact__role { margin-bottom: 18px; }
  .contact__address { margin-bottom: 16px; }
  .contact__line {
    display: flex;
    align-items: center;
    gap: 8px;
    margin-bottom: 3px;
  }
  .contact__icon { width: 13px; height: 13px; flex-shrink: 0; }
</style>
</head>
<body>

  <section class="card card--front">
    <div class="brand">
      <span class="brand__dot"></span>
      <span>Meridian Care<br>Clinic</span>
    </div>
    <div class="card__edge"></div>
  </section>

  <section class="card card--back">
    <div class="brand">
      <span class="brand__dot"></span>
      <span>Meridian Care<br>Clinic</span>
    </div>

    <div class="divider"></div>

    <div class="contact">
      <p class="contact__name">Daniel Hartley</p>
      <p class="contact__role">Director/Founder</p>
      <p class="contact__address">1180 Harbor Lane<br>Lakeview Park CA 90210</p>

      <p class="contact__line">
        <svg class="contact__icon" viewBox="0 0 16 16" aria-hidden="true"><path fill="#29abe2" d="M3.5 1.5l2.6.4 1 3-1.7 1.3a8.5 8.5 0 0 0 4.4 4.4l1.3-1.7 3 1 .4 2.6-1.8 1.8C7.3 14.3 1.7 8.7 1.7 3.3z"/></svg>
        <span>0555 014 2207</span>
      </p>
      <p class="contact__line">
        <svg class="contact__icon" viewBox="0 0 16 16" aria-hidden="true"><rect x="1.5" y="3.5" width="13" height="9" rx="1" fill="none" stroke="#29abe2" stroke-width="1.6"/><path d="M1.8 4l6.2 5 6.2-5" fill="none" stroke="#29abe2" stroke-width="1.6"/></svg>
        <span>info@meridiancareclinic.com</span>
      </p>
      <p class="contact__line">
        <svg class="contact__icon" viewBox="0 0 16 16" aria-hidden="true"><circle cx="8" cy="8" r="6.3" fill="none" stroke="#29abe2" stroke-width="1.5"/><ellipse cx="8" cy="8" rx="2.7" ry="6.3" fill="none" stroke="#29abe2" stroke-width="1.2"/><path d="M1.7 8h12.6" stroke="#29abe2" stroke-width="1.2"/></svg>
        <span>www.meridiancareclinic.com</span>
      </p>
    </div>

    <div class="card__edge"></div>
  </section>

</body>
</html>
```